International oil and gas consultancy needs a business card design

We need a business card design for a new oil and gas consultancy business based in Perth Australia. This is a professional services business and needs a moderately conservative type of business card. The business card also needs to be simple and uncluttered. The colour of the business logo is dark red (see attached file).
The front of the card should have a white background and mainly black lettering and perhaps some use of dark red and/or grey (your choice).
The back of the card should have a light grey background with dark red, black and or both dark red & black lettering (your choice).
Please find attached a clear brief of how I would like the business card designed.
Updates

Hello Everyone, I have slightly modified the brief. The main change is to incorporate some dark red and grey colours into the card, while still keeping the black lettering dominant. I have made the changes in the attached detailed brief document. Regards

Please note, the front of the card must say Harbour Ledger Services (in addition to the logo).

Industry/Entity Type

Conservative

Requirements
Must have
• brief has been updated. please refer to attachment for details.

Front of the card MUST say Harbour Ledger Services (in addition to the logo)

```html
<!DOCTYPE html>
<html lang="en">
<head>
<meta charset="utf-8">
<title>Harbour Ledger Services — Business Card</title>
<link rel="stylesheet" href="https://fonts.googleapis.com/css2?family=Exo+2:wght@400;600;800&display=swap">
<style>
  :root {
    --brand-red: #951b1e;
    --paper: #ffffff;
    --backdrop: #e9e9ea;
    --tab-grey: #9a9a9a;
    --ink-light: #ffffff;
  }
  * { margin: 0; padding: 0; box-sizing: border-box; }
  html, body { width: 1200px; height: 905px; overflow: hidden; }
  body {
    background: var(--backdrop);
    font-family: "Exo 2", sans-serif;
    display: flex;
    align-items: center;
    justify-content: center;
    gap: 48px;
  }
  .card {
    width: 540px;
    height: 310px;
    background: var(--paper);
    box-shadow: 0 2px 6px rgba(0,0,0,0.12);
    position: relative;
    overflow: hidden;
  }
  .card-front { display: flex; }
  .contact-panel {
    width: 56%;
    background: var(--brand-red);
    color: var(--ink-light);
    padding: 34px 0 0 30px;
    position: relative;
  }
  .tab-accent {
    position: absolute;
    top: 24px;
    left: 30px;
    width: 22px;
    height: 26px;
    background: var(--tab-grey);
  }
  .person {
    margin-left: 36px;
    margin-top: 6px;
  }
  .person-name {
    font-size: 15px;
    font-weight: 400;
    letter-spacing: 0.06em;
  }
  .person-role {
    font-size: 14px;
    font-weight: 400;
    margin-top: 2px;
  }
  .contact-grid {
    display: grid;
    grid-template-columns: auto auto;
    column-gap: 18px;
    row-gap: 8px;
    margin-top: 42px;
    font-size: 10.5px;
    letter-spacing: 0.02em;
  }
  .contact-item { display: flex; align-items: center; gap: 6px; white-space: nowrap; }
  .contact-item svg { width: 10px; height: 10px; flex: none; }
  .address {
    margin-top: 12px;
    font-size: 12.5px;
    letter-spacing: 0.03em;
  }
  .brand-panel {
    flex: 1;
    display: flex;
    align-items: center;
    justify-content: center;
    padding: 0 20px;
  }
  .brand-name {
    color: var(--brand-red);
    font-weight: 800;
    font-size: 22px;
    line-height: 1.15;
    text-align: center;
    letter-spacing: 0.01em;
  }
  .card-back {
    display: flex;
    align-items: center;
    justify-content: center;
  }
  .card-back .brand-name { font-size: 32px; }
</style>
</head>
<body>
  <section class="card card-front" aria-label="Business card front">
    <div class="contact-panel">
      <span class="tab-accent"></span>
      <div class="person">
        <p class="person-name">MARTIN HOLLOWAY</p>
        <p class="person-role">Managing Director</p>
      </div>
      <div class="contact-grid">
        <span class="contact-item">
          <svg viewBox="0 0 10 10" aria-hidden="true"><rect x="2.5" y="0.5" width="5" height="9" rx="1" fill="none" stroke="currentColor"/><rect x="4" y="7.3" width="2" height="1" fill="currentColor"/></svg>
          012 555 0142
        </span>
        <span class="contact-item">
          <svg viewBox="0 0 10 10" aria-hidden="true"><rect x="0.5" y="2" width="9" height="6" fill="none" stroke="currentColor"/><path d="M0.5 2 L5 5.5 L9.5 2" fill="none" stroke="currentColor"/></svg>
          info@harbourledger.com
        </span>
        <span class="contact-item">
          <svg viewBox="0 0 10 10" aria-hidden="true"><path d="M2 0.8 L3.8 2.8 L2.8 4 Q4 6.3 6 7.2 L7.2 6.2 L9.2 8 L8 9.3 Q3 8.5 0.8 2 Z" fill="currentColor"/></svg>
          012 555 0143
        </span>
        <span class="contact-item">
          <svg viewBox="0 0 10 10" aria-hidden="true"><circle cx="5" cy="5" r="4.5" fill="none" stroke="currentColor"/><ellipse cx="5" cy="5" rx="2" ry="4.5" fill="none" stroke="currentColor"/><path d="M0.5 5 H9.5" stroke="currentColor"/></svg>
          www.harbourledger.com
        </span>
      </div>
      <p class="address">041 9th Floor Quay Street Perth WA</p>
    </div>
    <div class="brand-panel">
      <p class="brand-name">Harbour Ledger Services</p>
    </div>
  </section>

  <section class="card card-back" aria-label="Business card back">
    <p class="brand-name">Harbour Ledger Services</p>
  </section>
</body>
</html>
```